Smile club flyer design

I am launching an office smile club and would like a design that sits my branding and that is appealing to customers. I have a design (I need a new one) that has all the information.
My website is maplehavendentalcarekx.com
Brand color is green. The design can be any color

Target Market(s)

Ages 30+

Industry/Entity Type

Dental

Font styles to use
Serif

Requirements
Must have
• Appealing to patients

```html
<!DOCTYPE html>
<html lang="en">
<head>
<meta charset="utf-8">
<title>Smile Club Membership – Maplehaven Dental Care</title>
<link href="https://fonts.googleapis.com/css2?family=Bebas+Neue&family=Great+Vibes&family=Montserrat:wght@600;700;800&family=Playfair+Display:wght@700;900&family=Roboto+Condensed:wght@500;600&display=swap" rel="stylesheet">
<style>
:root{
  --backdrop:#1f1f1f;
  --green-dark:#0b8a3b;
  --green-deep:#0b5a2a;
  --green-mid:#138a3d;
  --green-light:#8fd14f;
  --green-pale:#e4f6c4;
  --ink:#1a2a1f;
  --white:#ffffff;
}
*{margin:0;padding:0;box-sizing:border-box}
html,body{width:956px;height:1200px;overflow:hidden;background:var(--backdrop)}
.flyer{position:absolute;left:88px;top:15px;width:780px;height:1170px;background:var(--white);overflow:hidden;font-family:"Montserrat",sans-serif}
.shapes{position:absolute;left:0;top:0}
.photo{position:absolute;left:200px;top:0;width:580px;height:480px;
  background:radial-gradient(ellipse at 62% 40%,#f1ddd0 0%,#e8d4c8 30%,rgba(214,228,238,.9) 62%,rgba(255,255,255,0) 85%),
  linear-gradient(90deg,#ffffff 0%,rgba(255,255,255,0) 40%),linear-gradient(180deg,#eef2f5,#cfe2ee);}
.brand{position:absolute;left:540px;top:38px;width:240px;text-align:center;color:var(--white)}
.brand-name{font-family:"Playfair Display",serif;font-weight:700;font-size:31px;line-height:1}
.brand-sub{font-family:"Montserrat",sans-serif;font-weight:600;font-size:11px;letter-spacing:4px;margin-top:6px}
.intro{position:absolute;left:44px;top:50px;font-family:"Great Vibes",cursive;font-size:54px;color:var(--green-deep);line-height:1}
.headline{position:absolute;left:42px;top:106px;font-family:"Playfair Display",serif;font-weight:900;font-size:55px;line-height:60px;letter-spacing:-.5px}
.headline .l1{color:var(--green-mid);display:block}
.headline .l2{color:var(--green-deep);display:block}
.pill{position:absolute;border-radius:21px;font-weight:700;font-size:18px;display:flex;align-items:center;padding-left:21px}
.pill-light{left:41px;top:236px;width:333px;height:41px;background:var(--green-light);color:var(--green-deep)}
.pill-dark{left:41px;top:282px;width:333px;height:41px;background:var(--green-dark);color:var(--white);border:2px solid var(--green-light)}
.card{position:absolute;width:229px;background:var(--white);border:2px solid #c9ec9a;border-radius:10px}
.card-core{left:30px;top:493px;height:309px}
.card-bright{left:275px;top:431px;height:309px}
.card-total{left:510px;top:493px;height:309px}
.card-rule{position:absolute;left:0;right:0;height:2px;background:#b6e37a}
.badge{position:absolute;width:174px;height:174px;border-radius:50%;text-align:center;display:flex;flex-direction:column;align-items:center;justify-content:center}
.badge-dark{background:var(--green-dark);color:var(--white);box-shadow:0 9px 0 var(--green-light)}
.badge-light{background:var(--green-light);color:var(--green-deep);box-shadow:0 9px 0 var(--green-dark)}
.badge-name{font-family:"Bebas Neue",sans-serif;font-size:33px;line-height:.95}
.badge-name.big{font-size:40px}
.badge-tier{font-weight:600;font-size:12.5px;letter-spacing:.3px}
.badge-price{font-family:"Bebas Neue",sans-serif;font-size:56px;line-height:1;margin-top:4px}
.badge-unit{font-weight:600;font-size:10px}
.features{position:absolute;list-style:none;font-family:"Roboto Condensed",sans-serif;font-weight:600;font-size:14px;line-height:19px;color:var(--ink)}
.features li{position:relative;padding-left:19px;margin-bottom:7px}
.features li::before{content:"";position:absolute;left:0;top:3px;width:13px;height:13px;border-radius:50%;background:var(--green-dark)}
.features li::after{content:"";position:absolute;left:4px;top:5.5px;width:3px;height:6px;border:solid var(--white);border-width:0 2px 2px 0;transform:rotate(45deg)}
.price-tag{position:absolute;height:40px;border-radius:20px;background:var(--green-dark);color:var(--white);font-weight:700;font-size:20px;display:flex;align-items:center;justify-content:center;border:2px solid #c9ec9a}
.band{position:absolute;left:0;top:918px;width:780px;height:104px;background:var(--green-light)}
.finance{position:absolute;left:27px;top:952px;font-weight:800;font-size:21px;line-height:27px;color:var(--green-deep)}
.join{position:absolute;left:520px;top:936px;width:242px;text-align:center;font-weight:800;font-size:29px;line-height:35px;color:var(--green-deep)}
.package{position:absolute;left:275px;top:872px;width:229px;height:202px;background:var(--green-dark);border-radius:10px}
.package-badge{position:absolute;left:301px;top:797px;width:180px;height:180px;border-radius:50%;background:var(--green-light);border:7px solid var(--white);color:var(--green-deep);text-align:center;display:flex;flex-direction:column;align-items:center;justify-content:center}
.package-new{font-family:"Great Vibes",cursive;font-size:28px;line-height:1;margin-top:4px}
.package-name{font-weight:800;font-size:32px;line-height:1}
.package-sub{font-weight:700;font-size:11.5px;margin-top:2px}
.package-price{font-family:"Bebas Neue",sans-serif;font-size:56px;line-height:1;margin-top:2px}
.package .features{left:17px;top:125px;width:196px;color:var(--green-light)}
.package .features li::before{background:var(--green-light)}
.package .features li::after{border-color:var(--green-dark)}
.package-rule{position:absolute;left:0;right:0;top:165px;height:2px;background:var(--green-light)}
.offer{position:absolute;left:15px;top:182px;width:199px;height:40px;border-radius:20px;background:var(--green-light);color:var(--green-deep);font-weight:700;font-size:14px;display:flex;align-items:center;justify-content:center;border:2px solid var(--white)}
.partners{position:absolute;left:24px;top:1034px;font-weight:800;color:var(--green-deep)}
.partner{display:flex;align-items:center;gap:8px;font-size:27px;line-height:38px}
.partner-mark{width:18px;height:18px;border-radius:50%;background:var(--green-dark)}
.contact{position:absolute;left:520px;top:1037px;width:242px;text-align:center}
.phone-icon{display:block;margin:0 auto}
.phone{font-weight:800;font-size:31px;color:var(--green-deep);margin-top:3px;letter-spacing:.5px}
.footer{position:absolute;left:0;top:1128px;width:780px;height:42px;background:var(--green-dark);color:var(--white)}
.footer-left{position:absolute;left:66px;top:11px;font-weight:600;font-size:16px}
.footer-right{position:absolute;left:340px;top:9px;font-family:"Roboto Condensed",sans-serif;font-weight:600;font-size:19px}
</style>
</head>
<body>
<main class="flyer">
  <div class="photo" role="img" aria-label="Photo of a smiling patient in a dental chair during a check-up"></div>

  <svg class="shapes" width="780" height="1170" viewBox="0 0 780 1170" aria-hidden="true">
    <defs>
      <linearGradient id="meadow" x1="0" y1="0" x2="0" y2="1">
        <stop offset="0" stop-color="#d8f29e"/>
        <stop offset=".5" stop-color="#eef9d6"/>
        <stop offset="1" stop-color="#e2f5b8"/>
      </linearGradient>
    </defs>
    <path d="M0 386 C150 450 250 482 390 486 C550 490 680 445 780 385 L780 1170 L0 1170Z" fill="url(#meadow)"/>
    <path d="M418 0 L780 0 L780 351 C760 380 720 365 705 330 C695 300 695 240 695 190 C695 150 670 130 640 128 C600 125 560 110 540 80 C515 40 480 20 418 0Z" fill="var(--green-dark)"/>
    <g fill="none" stroke="var(--green-dark)" stroke-width="2.5">
      <path d="M60 469 A98 98 0 0 1 230 469"/>
      <path d="M306 403 A98 98 0 0 1 476 403"/>
      <path d="M550 469 A98 98 0 0 1 720 469"/>
      <path d="M306 849 A98 98 0 0 1 476 849"/>
    </g>
    <g fill="var(--green-dark)">
      <circle cx="60" cy="469" r="4"/><circle cx="230" cy="469" r="4"/>
      <circle cx="306" cy="403" r="4"/><circle cx="476" cy="403" r="4"/>
      <circle cx="550" cy="469" r="4"/><circle cx="720" cy="469" r="4"/>
      <circle cx="306" cy="849" r="4"/><circle cx="476" cy="849" r="4"/>
    </g>
  </svg>

  <div class="brand">
    <div class="brand-name">Maplehaven</div>
    <div class="brand-sub">DENTAL CARE</div>
  </div>

  <div class="intro">Introducing</div>
  <h1 class="headline"><span class="l1">SMILE CLUB</span><span class="l2">MEMBERSHIP</span></h1>
  <div class="pill pill-light">AFFORDABLE DENTAL CARE</div>
  <div class="pill pill-dark">NO INSURANCE REQUIRED</div>

  <section class="card card-core">
    <ul class="features" style="left:16px;top:123px;width:200px">
      <li>Comprehensive Annual Exam</li>
      <li>2 Professional Cleanings per Year</li>
      <li>Routine Bitewing X-rays</li>
      <li>10% Savings on Treatment</li>
    </ul>
    <div class="card-rule" style="top:265px"></div>
  </section>
  <div class="badge badge-dark" style="left:58px;top:410px">
    <div class="badge-name">CORE CARE</div>
    <div class="badge-tier">PREVENTIVE</div>
    <div class="badge-price">$39</div>
    <div class="badge-unit">/MONTH</div>
  </div>
  <div class="price-tag" style="left:58px;top:777px;width:175px">$39/MONTH</div>

  <section class="card card-bright">
    <ul class="features" style="left:16px;top:122px;width:196px">
      <li>Annual In-Office Whitening (Top &amp; Bottom)</li>
      <li>Custom Whitening Trays</li>
      <li>15% Savings on Elective Treatment</li>
    </ul>
    <div class="card-rule" style="top:264px"></div>
  </section>
  <div class="badge badge-light" style="left:304px;top:348px">
    <div class="badge-name big">BRIGHT</div>
    <div class="badge-tier">COSMETIC</div>
    <div class="badge-price">$59</div>
    <div class="badge-unit">/MONTH</div>
  </div>
  <div class="price-tag" style="left:303px;top:714px;width:175px">$59/MONTH</div>

  <section class="card card-total">
    <ul class="features" style="left:16px;top:122px;width:200px">
      <li>3-4 Perio Maintenance Visits per Year</li>
      <li>1 Comprehensive Exam</li>
      <li>Diagnostic X-rays</li>
      <li>15% Savings on Restorative &amp; Elective Care</li>
    </ul>
    <div class="card-rule" style="top:264px"></div>
  </section>
  <div class="badge badge-dark" style="left:548px;top:410px">
    <div class="badge-name">TOTAL SMILE</div>
    <div class="badge-tier">PERIODONTAL</div>
    <div class="badge-price">$89</div>
    <div class="badge-unit">/MONTH</div>
  </div>
  <div class="price-tag" style="left:548px;top:776px;width:175px">$89/MONTH</div>

  <div class="band"></div>
  <div class="finance">FLEXIBLE FINANCING<br>FOR TREATMENT</div>
  <div class="join">JOIN SMILE<br>CLUB TODAY!</div>

  <section class="package">
    <ul class="features">
      <li>Cleaning + Comprehensive Exam + Whitening</li>
    </ul>
    <div class="package-rule"></div>
    <div class="offer">LIMITED TIME OFFER</div>
  </section>
  <div class="package-badge">
    <div class="package-new">New</div>
    <div class="package-name">SMILE</div>
    <div class="package-sub">REFRESH PACKAGE</div>
    <div class="package-price">$499</div>
  </div>

  <div class="partners">
    <div class="partner"><span class="partner-mark"></span>Fundwell</div>
    <div class="partner"><span class="partner-mark"></span>Bloomly</div>
  </div>

  <div class="contact">
    <svg class="phone-icon" width="34" height="34" viewBox="0 0 34 34" aria-hidden="true">
      <circle cx="17" cy="17" r="17" fill="var(--green-dark)"/>
      <path d="M12.5 9.5l2.6 3.2-1.6 1.9c.9 2 2.6 3.7 4.6 4.6l1.9-1.6 3.2 2.6-1.5 3c-5.6-.3-11.3-6-11.6-11.6z" fill="var(--white)"/>
      <path d="M19 10.5a5 5 0 0 1 4.5 4.5M19 7.5a8 8 0 0 1 7.5 7.5" fill="none" stroke="var(--white)" stroke-width="1.5" stroke-linecap="round"/>
    </svg>
    <div class="phone">865-555-0142</div>
  </div>

  <footer class="footer">
    <div class="footer-left">PAYMENT PLANS AVAILABLE</div>
    <div class="footer-right">*$49 Lifetime Activation Fee (Non-Refundable)</div>
  </footer>
</main>
</body>
</html>
```